Real Estate Newsletter

I would like a template created for a monthly newsletter; ideally, two pages long, including my photo, logo and contact info. I need it to look professional and be very easy for me to drop text into.

Target Market(s)

Past/current clients

Industry/Entity Type

Real Estate Agent

Font styles to use
Serif

Requirements
Must have
• My contact info/photo and logo
• (206) 555-0173
• mkorvell@tlxhb.com
• www.MarenKorvell.com
Nice to have
• I need a template where I can easily drop contact. I need the template to look professional so I can print it and mail it to current and past clients.

```html
<!DOCTYPE html>
<html lang="en">
<head>
<meta charset="utf-8">
<title>MarenKorvell Newsletter Template</title>
<link rel="stylesheet" href="https://fonts.googleapis.com/css2?family=Libre+Baskerville:wght@400;700&display=swap">
<style>
  :root{
    --ink:#2e3192;
    --lavender-col:#e3e3f2;
    --mauve:#d4b6d8;
    --mat:#d6d7da;
    --paper:#ffffff;
    --frame:#111111;
    --photo-tone:#b9a49a;
  }
  *{box-sizing:border-box;margin:0;padding:0}
  html,body{width:1200px;height:1200px;overflow:hidden;background:var(--paper)}
  body{position:relative;font-family:"Libre Baskerville",Georgia,serif;color:var(--ink)}
  .mat{position:absolute;left:210px;top:50px;width:785px;height:1103px;background:var(--mat)}
  .page{position:absolute;left:228px;top:70px;width:750px;height:1062px;background:var(--paper);border:2px solid var(--frame);overflow:hidden}
  .sidebar{position:absolute;left:17px;top:0;width:249px;height:100%;background:var(--lavender-col)}
  .header-band{position:absolute;left:0;top:66px;width:100%;height:101px;background:var(--mauve)}
  .portrait{position:absolute;left:74px;top:49px;width:140px;height:140px;border-radius:50%;background:var(--mauve);display:flex;align-items:center;justify-content:center}
  .portrait-fill{width:128px;height:128px;border-radius:50%;background:radial-gradient(circle at 55% 40%,#e9dcd3 0%,var(--photo-tone) 55%,#5a4338 100%)}
  .brand{position:absolute;left:384px;top:99px;width:240px;display:flex;align-items:center;justify-content:center;gap:8px;font-size:19px;font-weight:700;color:var(--ink)}
  .brand-dot{width:10px;height:10px;border-radius:50%;background:var(--ink)}
  .rule{position:absolute;left:35px;width:213px;border-top:1.5px dashed var(--ink)}
  .side-title{position:absolute;left:17px;width:249px;text-align:center;font-size:16px;letter-spacing:2.5px}
  .contact-icon{position:absolute;left:135px;width:16px;height:16px}
  .contact-text{position:absolute;left:17px;width:249px;text-align:center;font-size:12.5px;letter-spacing:.6px}
  .date-text{position:absolute;left:35px;font-size:12.5px;letter-spacing:.6px}
  .date-text sup{font-size:7px}
  .field{position:absolute;left:35px;width:215px;font-size:12.5px;letter-spacing:.5px}
  .field .label{position:absolute;left:0}
  .field .colon{position:absolute;left:99px}
  .field .line{position:absolute;left:109px;right:0;top:9px;border-top:1.5px dotted var(--ink)}
  .section-bar{position:absolute;left:294px;width:424px;height:38px;background:var(--mauve);display:flex;align-items:center;justify-content:center;font-size:12.5px;letter-spacing:.8px}
  .section-body{position:absolute;left:294px;width:424px;text-align:center;font-size:12.5px;line-height:15.15px;letter-spacing:.6px}
</style>
</head>
<body>
<div class="mat"></div>
<div class="page">
  <div class="sidebar"></div>
  <div class="header-band"></div>
  <div class="portrait"><div class="portrait-fill" role="img" aria-label="Portrait photo of the agent"></div></div>
  <div class="brand"><span class="brand-dot"></span>MarenKorvell</div>

  <div class="rule" style="top:214px"></div>
  <div class="side-title" style="top:228px">CONTACT</div>
  <div class="rule" style="top:265px"></div>

  <svg class="contact-icon" style="top:288px" viewBox="0 0 16 16" aria-hidden="true"><circle cx="8" cy="8" r="8" fill="#111"/><path d="M5 4.5l1.6-.3.8 2-1 .8c.5 1.1 1.3 1.9 2.4 2.4l.8-1 2 .8-.3 1.6c-3.5.2-6.5-2.8-6.3-6.3z" fill="#fff"/></svg>
  <div class="contact-text" style="top:306px">(206) 555-0173</div>

  <svg class="contact-icon" style="top:343px" viewBox="0 0 16 16" aria-hidden="true"><circle cx="8" cy="8" r="7.2" fill="#fff" stroke="#111" stroke-width="1.5"/><rect x="4" y="5.3" width="8" height="5.6" fill="none" stroke="#111" stroke-width="1.1"/><path d="M4 5.3l4 3.2 4-3.2" fill="none" stroke="#111" stroke-width="1.1"/></svg>
  <div class="contact-text" style="top:359px">mkorvell@tlxhb.com</div>

  <svg class="contact-icon" style="top:394px" viewBox="0 0 16 16" aria-hidden="true"><circle cx="8" cy="8" r="7" fill="none" stroke="#111" stroke-width="1.6"/><ellipse cx="8" cy="8" rx="3" ry="7" fill="none" stroke="#111" stroke-width="1.3"/><path d="M1 8h14M2 4.5h12M2 11.5h12" stroke="#111" stroke-width="1.2"/></svg>
  <div class="contact-text" style="top:414px">www.MarenKorvell.com</div>

  <div class="rule" style="top:495px"></div>
  <div class="side-title" style="top:509px">DATE</div>
  <div class="rule" style="top:546px"></div>
  <div class="date-text" style="top:563px">[example] 12<sup>th</sup> February 2018</div>

  <div class="rule" style="top:660px"></div>
  <div class="side-title" style="top:674px">TO :</div>
  <div class="rule" style="top:711px"></div>

  <div class="field" style="top:730px"><span class="label">Client Name</span><span class="colon">:</span><span class="line"></span></div>
  <div class="field" style="top:760px"><span class="label">Phone</span><span class="colon">:</span><span class="line"></span></div>
  <div class="field" style="top:790px"><span class="label">Email</span><span class="colon">:</span><span class="line"></span></div>
  <div class="field" style="top:820px"><span class="label">Address</span><span class="colon">:</span><span class="line"></span></div>

  <div class="section-bar" style="top:213px">Information</div>
  <div class="section-body" style="top:265px">Write your text here<br>Write your text here<br>Write your text her<br>Write your text here<br>Write your text here<br>Write your text here<br>Write your text here<br>Write your text here<br>Write your text here<br>Write your text here<br>Write your text here</div>

  <div class="section-bar" style="top:546px">Booking Confirmation</div>
  <div class="section-body" style="top:598px">Write your text here<br>Write your text here<br>Write your text her<br>Write your text here<br>Write your text here<br>Write your text here<br>Write your text here<br>Write your text here<br>Write your text here<br>Write your text here<br>Write your text here</div>

  <div class="section-bar" style="top:782px">Note</div>
  <div class="section-body" style="top:834px">Write your text here<br>Write your text here<br>Write your text her<br>Write your text here<br>Write your text here<br>Write your text here<br>Write your text here<br>Write your text here<br>Write your text here<br>Write your text here<br>Write your text here</div>
</div>
</body>
</html>
```